Children's Chorus Flyer

Hello,

I need a flyer design (probably in two sizes 8x11, 5x7) that promotes my community children's chorus and also announces our summer camp. I would like a flyer that is playful and eye-catching while remaining somewhat simplistic. It should have our logo (will upload that) and either some cartoon graphics or pictures of the current kids or both. Although it does not have to have the picture of the kids. I'm leaving it up to you. I am uploading an example of a flyer that I like to help guide you. It needs to have this basic info:

"Do you love to sing? The Maple Sparrows is looking for boys and girls ages 7-16 to audition for the 2012-2013 season! Rehearsals are held weekly at Bramble Hollow Presbyterian Church (27806 Fenwick Ridge Rd). Contact us for an audition appointment.

Summer Choral Camp!
The Maple Sparrows is planning a 2-week choral camp where singers will have fun working on music reading skills, vocal technique, choreography and more! Boys and girls ages 7-16 are invited to enroll.

Dates: July 16-27
Times: 9am-3pm (extended care hours available at additional fee)
Tuition: $300 for 2-week session ($150 per week)

For more information, please visit our website: www.maplesparrowsingers.example, email: info@maplesparrowsingers.example or call 555.384.9152."

Target Market(s)

parents and children

Industry/Entity Type

Church

Requirements
Must have
• logo, basic info typed above.
Nice to have
• the picture of the kids, although not totally necessary. Leaving it up to your creative ideas.

```html
<!DOCTYPE html>
<html lang="en">
<head>
<meta charset="utf-8">
<title>The Maple Sparrows – Summer Choral Camp</title>
<link rel="stylesheet" href="https://fonts.googleapis.com/css2?family=Didact+Gothic&family=Fredoka:wght@600&family=Signika:wght@600;700&family=Sniglet:wght@800&display=swap">
<style>
  :root {
    --sky-top: #4b8f8a;
    --sky-mid: #7fb4ac;
    --grass: #8cc63f;
    --grass-deep: #5f9d2a;
    --panel: #fbfbe2;
    --brand-teal: #3f8a86;
    --headline-green: #8dc63f;
    --outline-green: #6aa82a;
    --body-grey: #555a55;
    --detail-green: #2c3a12;
    --choral-red: #e2402e;
    --white: #ffffff;
    --footer-text: #eef7e6;
  }
  * { box-sizing: border-box; margin: 0; padding: 0; }
  html, body { width: 894px; height: 1200px; overflow: hidden; background: var(--sky-top); }
  .flyer { position: relative; width: 894px; height: 1200px; overflow: hidden; font-family: "Didact Gothic", sans-serif; }

  .backdrop {
    position: absolute; inset: 0;
    background: linear-gradient(180deg, var(--sky-top) 0%, var(--sky-mid) 55%, #b7d98a 78%, var(--grass) 86%, var(--grass-deep) 100%);
  }
  .cloud-bank {
    position: absolute; left: -40px; top: -40px; width: 420px; height: 250px;
    background: radial-gradient(ellipse at 40% 50%, #ffffff 55%, rgba(255,255,255,0) 72%);
  }
  .cloud-small { position: absolute; background: radial-gradient(ellipse, #ffffff 55%, rgba(255,255,255,0) 72%); }
  .cloud-right { left: 590px; top: 76px; width: 170px; height: 80px; }
  .cloud-left { left: -30px; top: 404px; width: 110px; height: 70px; }

  .brand { position: absolute; left: 52px; top: 72px; display: flex; align-items: center; gap: 12px; }
  .brand-dot { width: 30px; height: 30px; border-radius: 50%; background: var(--brand-teal); }
  .brand-name { font-size: 34px; color: var(--brand-teal); line-height: 1.05; width: 200px; }

  .panel {
    position: absolute; left: 72px; top: 222px; width: 756px; height: 820px;
    border-radius: 24px 24px 0 0;
    background: linear-gradient(180deg, var(--panel) 0%, var(--panel) 72%, rgba(251,251,226,0) 100%);
  }

  .headline {
    position: absolute; left: 100px; top: 228px; width: 340px;
    font-family: "Fredoka", sans-serif; font-weight: 600; color: var(--headline-green);
  }
  .headline .line { height: 56px; line-height: 70px; white-space: nowrap; }
  .headline .big { font-size: 76px; }
  .headline .small { font-size: 46px; }
  .headline .line1 { margin-left: 40px; }
  .headline .line3 { margin-left: 40px; }

  .audition-text {
    position: absolute; left: 470px; top: 248px; width: 320px;
    font-size: 15.5px; line-height: 29px; color: var(--body-grey);
  }

  .divider { position: absolute; left: 126px; top: 452px; width: 630px; border-top: 4px dotted var(--brand-teal); opacity: 0.55; }

  .camp-title {
    position: absolute; left: 0; top: 460px; width: 894px; height: 150px;
    font-family: "Sniglet", sans-serif; font-weight: 800; color: var(--headline-green); white-space: nowrap;
  }
  .camp-title .word {
    position: absolute; top: 38px; font-size: 86px; line-height: 1;
    -webkit-text-stroke: 4px var(--outline-green); paint-order: stroke fill;
    text-shadow: 3px 3px 0 var(--white);
  }
  .camp-title .summer { left: 44px; }
  .camp-title .camp { left: 560px; }
  .camp-title .choral {
    position: absolute; left: 524px; top: 0; font-size: 38px; line-height: 1; color: var(--choral-red);
    -webkit-text-stroke: 5px var(--white); paint-order: stroke fill; transform: rotate(-4deg);
  }
  .caret { position: absolute; left: 536px; top: 70px; }

  .kids-art {
    position: absolute; left: 0; top: 640px; width: 300px; height: 560px;
    border-radius: 0 140px 0 0;
    background: linear-gradient(170deg, rgba(244,198,74,0.55) 0%, rgba(226,86,110,0.45) 30%, rgba(74,143,220,0.55) 65%, rgba(74,143,220,0.15) 100%);
  }

  .camp-text {
    position: absolute; left: 380px; top: 620px; width: 388px;
    font-size: 15.5px; line-height: 23px; color: var(--body-grey); text-align: right;
  }

  .details { position: absolute; right: 142px; top: 748px; text-align: right; font-family: "Signika", sans-serif; color: var(--detail-green); }
  .detail-line { font-weight: 700; font-size: 28px; line-height: 34px; }
  .detail-note { font-weight: 600; font-size: 14.5px; line-height: 18px; }
  .dates { margin-bottom: 26px; }
  .tuition { font-size: 31px; line-height: 38px; margin-top: 30px; }

  .contact { position: absolute; right: 40px; top: 1078px; color: var(--footer-text); text-align: right; }
  .contact-title { font-family: "Signika", sans-serif; font-weight: 700; font-size: 22px; color: var(--white); margin-bottom: 4px; }
  .contact-line { font-size: 15px; line-height: 21px; }
</style>
</head>
<body>
<main class="flyer">
  <div class="backdrop" role="img" aria-label="Teal sky with sun rays fading into green grass and a faint city skyline"></div>
  <div class="cloud-bank"></div>
  <div class="cloud-small cloud-right"></div>
  <div class="cloud-small cloud-left"></div>

  <header class="brand">
    <span class="brand-dot"></span>
    <span class="brand-name">The Maple Sparrows</span>
  </header>

  <div class="panel"></div>

  <h1 class="headline">
    <div class="line line1"><span class="big">Do</span> <span class="small">you</span></div>
    <div class="line line2"><span class="big">Love</span></div>
    <div class="line line3"><span class="small">to</span> <span class="big">sing?</span></div>
  </h1>

  <p class="audition-text">The Maple Sparrows is looking for boys and girls ages 7-16 to audition for the 2012-2013 season! Rehearsals are held weekly at Bramble Hollow Presbyterian Church (27806 Fenwick Ridge Rd). Contact us for an audition appointment.</p>

  <div class="divider"></div>

  <div class="kids-art" role="img" aria-label="Cartoon boy and girl singing into a vintage microphone while sitting on a large blue music note, with small colourful notes in the grass"></div>

  <h2 class="camp-title">
    <span class="word summer">SUMMER</span>
    <span class="choral">Choral</span>
    <svg class="caret" width="26" height="22" viewBox="0 0 26 22"><path d="M3 20 L13 4 L23 20" fill="none" stroke="#e2402e" stroke-width="4" stroke-linecap="round"/></svg>
    <span class="word camp">CAMP</span>
  </h2>

  <p class="camp-text">The Maple Sparrows is planning a 2-week choral camp where singers will have fun working on music reading skills, vocal technique, choreography and more! Boys and girls ages 7-16 are invited to enroll.</p>

  <section class="details">
    <div class="detail-line dates">Dates: July 16-27</div>
    <div class="detail-line">Times: 9am-3pm</div>
    <div class="detail-note">(extended care hours available at additional fee)</div>
    <div class="detail-line tuition">Tuition: $300 for 2-week session</div>
    <div class="detail-note">($150 per week)</div>
  </section>

  <footer class="contact">
    <div class="contact-title">For more information,</div>
    <div class="contact-line">www.maplesparrowsingers.example</div>
    <div class="contact-line">info@maplesparrowsingers.example</div>
    <div class="contact-line">555.384.9152</div>
  </footer>
</main>
</body>
</html>
```